BRINDLEWOOD EXTRA VIRGIN OLIVE OIL

I needs a design for an Australian Extra Virgin Olive Oil.

The label will go on a round clear bottle

The label size front and back is 145mm high x 60mm wide.

The important points for the design are as follows.

I want to see elegant olives on the label so that non English speaking markets can easily understand its olive oil. I want it too look classy . IT must also look Australian but I don't want to see kangaroos just colours that reflect Australia.

The mandatory info on front label will be

BRINDLEWOOD

Cold Pressed
EXTRA VIRGIN OLIVE OIL

AUSTRALIAN

1 litre

```html
<!DOCTYPE html>
<html lang="en">
<head>
<meta charset="utf-8">
<title>Brindlewood Extra Virgin Olive Oil – Front Label</title>
<link rel="stylesheet" href="https://fonts.googleapis.com/css2?family=Open+Sans:wght@700;800&family=PT+Sans:wght@700&family=Tinos:wght@700&display=swap">
<style>
  :root {
    --forest: #0b3a10;
    --lime: #8cc63f;
    --lime-text: #12481a;
    --butter: #f6ec8e;
    --white: #ffffff;
    --mist: #eef6df;
    --leaf-pale: #cfe6a6;
    --leaf-bright: #7fbf2a;
    --leaf-mid: #5f9a22;
    --leaf-deep: #2f5a14;
    --olive-dark: #14240c;
    --shade-top: #2f4a1e;
    --shade-mid: #22391a;
    --shade-low: #162a10;
  }
  * { margin: 0; padding: 0; box-sizing: border-box; }
  html, body {
    width: 1200px;
    height: 2900px;
    overflow: hidden;
    background: var(--forest);
  }
  .label {
    position: relative;
    width: 1200px;
    height: 2900px;
    background: var(--forest);
    overflow: hidden;
  }
  .brand-band {
    position: absolute;
    left: 0; top: 0;
    width: 1200px; height: 326px;
    display: flex; align-items: center; justify-content: center;
  }
  .brand-name {
    font-family: "Open Sans", Arial, sans-serif;
    font-weight: 700;
    font-size: 124px;
    line-height: 1;
    color: var(--white);
  }
  .origin-band {
    position: absolute;
    left: 0; top: 333px;
    width: 1200px; height: 142px;
    background: var(--lime);
    display: flex; align-items: center; justify-content: center;
  }
  .origin {
    font-family: "Open Sans", Arial, sans-serif;
    font-weight: 700;
    font-size: 76px;
    line-height: 1;
    color: var(--lime-text);
  }
  .product-band {
    position: absolute;
    left: 0; top: 475px;
    width: 1200px; height: 467px;
    text-align: center;
    font-family: "Tinos", "Times New Roman", serif;
    font-weight: 700;
    color: var(--butter);
    white-space: nowrap;
  }
  .grade {
    position: absolute;
    left: 0; right: 0; top: 50px;
    font-size: 146px;
    line-height: 1;
  }
  .product {
    position: absolute;
    left: 0; right: 0; top: 235px;
    font-size: 124px;
    line-height: 1;
  }
  .hero-image {
    position: absolute;
    left: 18px; top: 942px;
    width: 1164px; height: 1153px;
    background:
      radial-gradient(ellipse 38% 30% at 80% 34%, var(--leaf-bright) 0%, rgba(127,191,42,0.55) 45%, rgba(127,191,42,0) 100%),
      radial-gradient(ellipse 30% 26% at 62% 72%, var(--leaf-mid) 0%, rgba(95,154,34,0.5) 50%, rgba(95,154,34,0) 100%),
      radial-gradient(ellipse 20% 14% at 33% 44%, var(--olive-dark) 0%, rgba(20,36,12,0.45) 55%, rgba(20,36,12,0) 100%),
      linear-gradient(200deg, rgba(47,90,20,0) 45%, rgba(47,90,20,0.75) 100%),
      linear-gradient(160deg, var(--mist) 0%, var(--leaf-pale) 55%, #a8cf74 100%);
  }
  .feature-band {
    position: absolute;
    left: 0; top: 2095px;
    width: 1200px; height: 178px;
    display: flex; align-items: center;
    padding-left: 46px;
  }
  .feature, .volume {
    font-family: "PT Sans", Arial, sans-serif;
    font-weight: 700;
    color: var(--butter);
    line-height: 1;
    white-space: nowrap;
  }
  .feature { font-size: 108px; }
  .base-image {
    position: absolute;
    left: 0; top: 2273px;
    width: 1200px; height: 627px;
    background:
      radial-gradient(ellipse 34% 40% at 78% 62%, rgba(95,140,50,0.45) 0%, rgba(95,140,50,0) 100%),
      radial-gradient(ellipse 28% 30% at 30% 72%, rgba(20,36,12,0.6) 0%, rgba(20,36,12,0) 100%),
      linear-gradient(115deg, rgba(80,120,45,0.35) 0%, rgba(80,120,45,0) 45%),
      linear-gradient(180deg, var(--shade-top) 0%, var(--shade-mid) 55%, var(--shade-low) 100%);
  }
  .volume {
    position: absolute;
    right: 52px; bottom: 52px;
    font-size: 116px;
  }
</style>
</head>
<body>
  <main class="label">
    <header class="brand-band">
      <h1 class="brand-name">BRINDLEWOOD</h1>
    </header>
    <div class="origin-band">
      <p class="origin">AUSTRALIAN</p>
    </div>
    <section class="product-band">
      <p class="grade">EXTRA VIRGIN</p>
      <p class="product">• OLIVE OIL •</p>
    </section>
    <div class="hero-image" role="img" aria-label="Photograph of glossy green olives and one black olive on a branch with slender olive leaves"></div>
    <div class="feature-band">
      <p class="feature">• Cold Pressed</p>
    </div>
    <div class="base-image" role="img" aria-label="Dark, faded echo of the olive branch photograph">
      <p class="volume">1 litre</p>
    </div>
  </main>
</body>
</html>
```